African homeware retailer needs a web page design

We need a web page design for a new homeware and accessories store based in Johannesburg, South Africa. Our store carries modern African inspired items from designers that support social development and poverty alleviation initiatives. We have a particular preference for outfits that are centred on the empowerment of women.

Our business celebrates the skill, design and product of African craft and the work of designers looking to take that forward in a socially beneficial way (creating employment, developing skills, supporting local crafts people etc). We aim to carry items and inspirations from all over the African continent.

We would like to see a design that communicates African beauty and elegance without the typical tribal references that are made in reference to African craft or art.

We would like the web page to be stylish, uncomplicated, modern, captivating and appealing to the discerning customer. A similar value proposition is that of http://www.marlowtenwick.example/.

This is an e-commerce website which must be attractive to both individual buyers and design professionals so the website needs to look professional.

Here are links to some websites we like:
http://www.quenbyhollis.example/
http://www.dravelo.example/

Our logo is attached to the brief.

Target Market(s)

Our target market is female, age 20-50. However should not alienate the design conscious male customer therefore

Industry/Entity Type

E-Commerce

Requirements
Must have
• - A featured product banner which includes a photograph and text. This should be easy to edit as we will be changing the featured product regularly
- An easily expendable products section with categories. Examples of categories could be cushions, bedding, crockery etc. Should be easy to add new categories as well as new product pictures
- Home/landing page should be uncluttered
- Should use the logo and should be easy to change the logo which we have in various colour combinations. We plan to change the logo colours depending on circumstance e.g. make it red and white around Valentines day (similar to the way Vintrel frequently changes the logo on their landing page)

```html
<!DOCTYPE html>
<html lang="en">
<head>
<meta charset="utf-8">
<title>Sable Hearth – Homeware & Accessories</title>
<link href="https://fonts.googleapis.com/css2?family=Roboto:wght@300;400;500;700&display=swap" rel="stylesheet">
<style>
:root{
  --page-bg:#ececec;
  --paper:#ffffff;
  --ink:#333333;
  --muted:#777777;
  --line:#dddddd;
  --accent:#f04e2b;
  --accent-soft:#f07a5c;
  --green:#15855f;
  --teal:#0f7a62;
  --dark-bar:rgba(40,40,40,.82);
  --hero:#ead5ce;
}
*{box-sizing:border-box;margin:0;padding:0}
html,body{width:809px;height:1200px;overflow:hidden}
body{background:var(--page-bg);font-family:'Roboto',sans-serif;color:var(--ink);font-size:9px}
.page{position:absolute;left:94px;top:0;width:620px;height:1200px;background:var(--paper);border-top:2px solid #555}
.abs{position:absolute}
.top-links{right:8px;top:10px;font-size:7.5px;color:var(--muted);letter-spacing:.2px}
.top-links span{margin:0 5px}
.top-rule{left:7px;right:7px;top:26px;border-top:1px solid #eee}
.logo{left:8px;top:44px;width:86px;text-align:center;color:var(--accent);font-weight:500;font-size:15px;line-height:1.05;letter-spacing:1px}
.logo .mark{display:block;width:36px;height:36px;border-radius:50%;background:var(--accent);margin:0 auto 8px}
.call{left:321px;top:44px;font-size:7.5px;display:flex;align-items:center;gap:3px}
.call b{font-weight:400;font-size:10.5px;margin-left:2px}
.call i{font-style:normal;color:var(--green);font-size:8.5px;margin-left:3px}
.search{left:228px;top:62px;width:208px;height:26px;border:1px solid #ccc;display:flex}
.search span{flex:1;padding:8px 9px;color:#999;font-size:8px}
.search button{width:28px;border:0;background:var(--accent);display:flex;align-items:center;justify-content:center}
.auth{left:502px;top:43px;font-size:7px;color:#555;display:flex;gap:16px}
.auth div{display:flex;align-items:center;gap:4px}
.cart{left:500px;top:62px;display:flex;height:26px}
.cart .ico{width:28px;background:var(--green);display:flex;align-items:center;justify-content:center}
.cart .sum{margin-left:1px;width:84px;background:#555;color:#fff;font-size:7.5px;font-weight:500;display:flex;align-items:center;justify-content:center}
.nav{left:7px;top:133px;width:607px;height:28px;background:var(--green);display:flex;color:#fff;font-size:8.8px}
.nav div{padding:0 14px;display:flex;align-items:center;position:relative}
.nav div+div::before{content:"";position:absolute;left:0;top:8px;height:12px;border-left:1px solid rgba(255,255,255,.35)}
.nav .active{background:var(--accent);width:82px;justify-content:center}
.hero{left:7px;top:168px;width:607px;height:266px;background:var(--hero);border:1px solid #d4a89c;overflow:hidden}
.hero .cushions{position:absolute;left:30px;top:18px;width:290px;height:200px;border-radius:40% 40% 30% 30%;background:linear-gradient(135deg,#c23a35,#1f4e8c 45%,#f2b43c 70%,#1d5c4b)}
.hero .crafts{position:absolute;left:345px;top:60px;width:150px;height:150px;transform:rotate(45deg);background:linear-gradient(135deg,#e8e4dc,#8a6a3b 50%,#4d3a20)}
.hero .arrow{position:absolute;top:122px;width:18px;height:18px;border-radius:50%;background:#fff;border:1px solid #ccc;display:flex;align-items:center;justify-content:center}
.hero .caption{position:absolute;left:10px;bottom:8px;width:300px;height:29px;background:linear-gradient(90deg,rgba(90,90,90,.9),rgba(90,90,90,.2));color:#fff;font-weight:300;font-size:15px;padding:5px 8px}
.hero .buy{position:absolute;left:257px;bottom:11px;background:var(--green);color:#fff;font-size:10px;padding:4px 11px;font-weight:500}
.cat-title{left:7px;top:447px;width:607px;height:25px;background:var(--accent-soft);color:#fff;font-weight:500;font-size:10.5px;text-align:center;line-height:25px;letter-spacing:.3px}
.tile{width:192px;height:211px;border:1px solid #ddd;overflow:hidden}
.tile .photo{position:absolute;inset:0}
.tile .save{position:absolute;right:0;bottom:30px;background:var(--teal);color:#fff;padding:2px 5px;text-align:center}
.tile .save small{display:block;font-size:5.5px;font-weight:500}
.tile .save b{font-size:11px}
.tile .bar{position:absolute;left:0;right:0;bottom:0;height:30px;background:var(--dark-bar);color:#fff;display:flex}
.tile .bar .name{width:111px;padding:9px 10px;font-size:10.5px;border-right:1px solid rgba(255,255,255,.4)}
.tile .bar .shop{flex:1;font-size:8px;display:flex;align-items:center;justify-content:center;gap:6px}
.rule{left:7px;width:607px;border-top:1px solid var(--line)}
.h{font-size:8.8px;font-weight:500;color:#333}
.social{display:flex;gap:8px;margin-top:14px}
.social span{width:15px;height:15px;background:#4a7bbf;border-radius:2px}
.news p{font-size:7.5px;margin-top:8px;color:#444}
.news .field{margin-top:10px;display:flex;width:197px;height:22px;border:1px solid #ccc}
.news .field span{flex:1;font-size:6.8px;color:#888;padding:6px 4px}
.news .field b{width:27px;background:var(--accent);color:#fff;font-size:7.5px;display:flex;align-items:center;justify-content:center}
.fb-box{display:flex;gap:6px;margin-top:9px;align-items:flex-start}
.fb-box .card{width:92px;height:46px;border:1px solid #ddd;display:flex;align-items:center;justify-content:center;color:var(--accent);font-size:10px;font-weight:500}
.fb-box .like{font-size:6.3px;color:#555;padding-top:6px}
.fb-box .like span{display:inline-block;border:1px solid #ccc;padding:1px 4px;margin-bottom:6px}
.col ul{list-style:none;margin-top:8px}
.col li{font-size:8.3px;color:#444;line-height:14.3px}
.col li::before{content:"»";margin-right:5px}
.divider{border-left:1px solid #e2e2e2}
.contact div{display:flex;gap:9px;font-size:8.3px;color:#444;line-height:13px;margin-top:7px}
.logo-foot{left:528px;top:1058px;width:80px;text-align:center;color:var(--accent);font-size:13px;font-weight:500;line-height:1.1;letter-spacing:1px}
.logo-foot .mark{display:block;width:32px;height:32px;border-radius:50%;background:var(--accent);margin:0 auto 10px}
.copy{left:13px;top:1176px;font-size:8.3px;color:#444}
.cards{right:10px;top:1172px;display:flex;gap:3px}
.cards span{width:28px;height:17px;border-radius:2px}
</style>
</head>
<body>
<div class="page">
  <div class="abs top-links">MY ACCOUNT<span>|</span>MY CART<span>|</span>MY WHISH LIST<span>|</span>CONTACT US</div>
  <div class="abs top-rule"></div>

  <div class="abs logo"><span class="mark"></span>SABLE<br>HEARTH</div>

  <div class="abs call">
    <svg width="10" height="10" viewBox="0 0 10 10"><circle cx="5" cy="5" r="4.4" fill="none" stroke="#555" stroke-width=".8"/><path d="M3.4 2.8l1 1-.6.7c.4.8 1 1.4 1.8 1.8l.7-.6 1 1-.8.8c-1.9-.3-3.6-2-3.9-3.9z" fill="#555"/></svg>
    Call Us: <b>011 555 0148</b><i>(24x7)</i>
  </div>

  <div class="abs search"><span>Search...</span><button aria-label="Search"><svg width="12" height="12" viewBox="0 0 12 12"><circle cx="5" cy="5" r="3.5" fill="none" stroke="#fff" stroke-width="1.6"/><path d="M7.6 7.6L11 11" stroke="#fff" stroke-width="1.8"/></svg></button></div>

  <div class="abs auth">
    <div><svg width="8" height="9" viewBox="0 0 8 9"><rect x="1" y="4" width="6" height="5" fill="#444"/><path d="M2.2 4V2.6a1.8 1.8 0 013.6 0V4" fill="none" stroke="#444"/></svg>LOGIN</div>
    <div><svg width="9" height="9" viewBox="0 0 9 9"><rect x=".5" y="1.5" width="7" height="7" fill="none" stroke="#444"/><path d="M3 6l5-5" stroke="#444" stroke-width="1.2"/></svg>SIGN UP</div>
  </div>

  <div class="abs cart">
    <div class="ico"><svg width="13" height="11" viewBox="0 0 13 11"><path d="M1 1h2l1.5 6h6l1.3-4.5H4" fill="none" stroke="#fff" stroke-width="1.1"/><circle cx="5.5" cy="9.3" r="1" fill="#fff"/><circle cx="9.7" cy="9.3" r="1" fill="#fff"/></svg></div>
    <div class="sum">0 items(s) - $0.00 &nbsp;▾</div>
  </div>

  <nav class="abs nav">
    <div class="active">SHOP NOW</div>
    <div>CUSHIONS</div><div>BEDDING</div><div>CROCKERY</div><div>SALE</div><div>DESIGNER &amp; ARCHITECTS</div><div>PRESS &amp; MENTIONS</div>
  </nav>

  <section class="abs hero">
    <div class="cushions" role="img" aria-label="Pile of colourful striped cushions"></div>
    <div class="crafts" role="img" aria-label="Woven baskets and fine crockery arranged in diamonds"></div>
    <div class="arrow" style="left:7px"><svg width="6" height="8"><path d="M5 1L1.5 4 5 7" fill="none" stroke="#333" stroke-width="1.4"/></svg></div>
    <div class="arrow" style="right:7px"><svg width="6" height="8"><path d="M1 1l3.5 3L1 7" fill="none" stroke="#333" stroke-width="1.4"/></svg></div>
    <div class="caption">Homeware &amp; Accessories</div>
    <div class="buy">BUY NOW</div>
  </section>

  <div class="abs cat-title">TOP CATEGORIES</div>

  <div class="abs tile" style="left:7px;top:484px"><div class="photo" role="img" aria-label="Cushions on a sofa by a window" style="background:linear-gradient(160deg,#b9c9a0,#8a5a6a 50%,#c2a46c)"></div><div class="save"><small>SAVE UP TO</small><b>40%</b></div><div class="bar"><div class="name">CUSHIONS</div><div class="shop">SHOP NOW ›</div></div></div>
  <div class="abs tile" style="left:214px;top:484px"><div class="photo" role="img" aria-label="Bed with coral patterned bedding" style="background:linear-gradient(160deg,#eee7dc,#e07b66 55%,#d9d0c4)"></div><div class="save"><small>SAVE UP TO</small><b>10%</b></div><div class="bar"><div class="name">BEDDING</div><div class="shop">SHOP NOW ›</div></div></div>
  <div class="abs tile" style="left:422px;top:484px"><div class="photo" role="img" aria-label="Patterned crockery table setting" style="background:linear-gradient(160deg,#8c6a4a,#e7e0d3 50%,#6b5a3c)"></div><div class="save"><small>SAVE UP TO</small><b>30%</b></div><div class="bar"><div class="name">CROCKERY</div><div class="shop">SHOP NOW ›</div></div></div>

  <div class="abs tile" style="left:7px;top:709px"><div class="photo" role="img" aria-label="Yellow chair with print cushion" style="background:linear-gradient(170deg,#f4f4f2 55%,#e2c437 70%,#8a6a4f)"></div><div class="save"><small>SAVE UP TO</small><b>20%</b></div><div class="bar"><div class="name">CHAIRS</div><div class="shop">SHOP NOW ›</div></div></div>
  <div class="abs tile" style="left:214px;top:709px"><div class="photo" role="img" aria-label="Colourful bangles and fabric goods" style="background:linear-gradient(160deg,#c8355a,#1a8c86 45%,#2a2a4a)"></div><div class="save"><small>SAVE UP TO</small><b>5%</b></div><div class="bar"><div class="name">HIPPIE</div><div class="shop">SHOP NOW ›</div></div></div>
  <div class="abs tile" style="left:422px;top:709px"><div class="photo" role="img" aria-label="Carved wooden candle holders" style="background:linear-gradient(90deg,#eeeeec,#6a2a1f 35%,#eeeeec 50%,#6a2a1f 75%,#eeeeec)"></div><div class="save"><small>SAVE UP TO</small><b>15%</b></div><div class="bar"><div class="name">AFRICAN CANDLE</div><div class="shop">SHOP NOW ›</div></div></div>

  <div class="abs rule" style="top:954px"></div>

  <div class="abs" style="left:9px;top:971px"><div class="h">FOLLOW US</div><div class="social"><span></span><span></span><span style="background:#444"></span><span style="background:#c33"></span><span style="background:#5ab"></span></div></div>
  <div class="abs divider" style="left:150px;top:970px;height:60px"></div>
  <div class="abs news" style="left:175px;top:971px"><div class="h">SIGN UP FOR NEWSLETTER</div><p>Signup Here Free Updates &amp; Latest OFFERS!</p><div class="field"><span>enter your email...</span><b>GO</b></div></div>
  <div class="abs divider" style="left:402px;top:970px;height:60px"></div>
  <div class="abs" style="left:435px;top:971px"><div class="h">FIND US ON FRIENDLOOP</div><div class="fb-box"><div class="card">SABLE HEARTH</div><div class="like"><span>Like</span><br>899 people like this.</div></div></div>

  <div class="abs rule" style="top:1045px"></div>

  <div class="abs col" style="left:9px;top:1060px"><div class="h">INFORMATIONS</div><ul><li>Our Blog</li><li>About Our Shop</li><li>Secure Shopping</li><li>Privacy Policy</li><li>Delivery Informations</li></ul></div>
  <div class="abs divider" style="left:118px;top:1060px;height:88px"></div>
  <div class="abs col" style="left:134px;top:1060px"><div class="h">CUSTOMER CARE</div><ul><li>Contact Us</li><li>Site Map</li><li>Top Sales &amp; Bestsellers</li><li>Gift Vouchers</li><li>Best Sellers</li></ul></div>
  <div class="abs divider" style="left:253px;top:1060px;height:88px"></div>
  <div class="abs col" style="left:267px;top:1060px"><div class="h">YOUR ACCOUNT</div><ul><li>Order Status</li><li>My Wishlist</li><li>Delivery Address</li><li>Order History</li><li>Newsletter</li></ul></div>
  <div class="abs divider" style="left:380px;top:1060px;height:88px"></div>
  <div class="abs contact" style="left:394px;top:1060px;width:140px"><div class="h">CONTACT US</div>
    <div><svg width="8" height="11" viewBox="0 0 8 11"><path d="M4 10.5S.5 6.3.5 4a3.5 3.5 0 017 0C7.5 6.3 4 10.5 4 10.5z" fill="#888"/><circle cx="4" cy="4" r="1.3" fill="#fff"/></svg><span>123 Lorem ipsum dolor sit amet ectetue euiolutpat.</span></div>
    <div><svg width="9" height="9" viewBox="0 0 10 10"><circle cx="5" cy="5" r="4.4" fill="none" stroke="#888"/><path d="M3.4 2.8l1 1-.6.7c.4.8 1 1.4 1.8 1.8l.7-.6 1 1-.8.8c-1.9-.3-3.6-2-3.9-3.9z" fill="#888"/></svg><span>011 555 0148</span></div>
    <div><svg width="9" height="8" viewBox="0 0 9 8"><rect x=".5" y="2" width="8" height="5.5" fill="none" stroke="#888"/><path d="M.5 2L4.5 5l4-3" fill="none" stroke="#888"/></svg><span>info@sablehearth.example</span></div>
  </div>
  <div class="abs logo-foot"><span class="mark"></span>SABLE<br>HEARTH</div>

  <div class="abs rule" style="top:1165px"></div>
  <div class="abs copy">Copyright © 2014 Sable Hearth. All rights reserved.</div>
  <div class="abs cards"><span style="background:#c8372d"></span><span style="background:#dbe4f0"></span><span style="background:#e6e6ea"></span><span style="background:#f0ece4"></span><span style="background:#1d4b9a"></span></div>
</div>
</body>
</html>
```